"Thornbury Accupuncture" needs a Promotional Card - A6 size

Requirements
Must have
• Bright colours, pictures of happy people, acupuncture-related pictures.

```html
<!DOCTYPE html>
<html lang="en">
<head>
<meta charset="utf-8">
<title>Thornbury Accupuncture – A6 Promotional Card</title>
<link href="https://fonts.googleapis.com/css2?family=Source+Sans+3:wght@300;400;600;700&display=swap" rel="stylesheet">
<style>
  :root {
    --stage: #8a8a8a;
    --white: #ffffff;
    --ink: #111111;
    --grey-text: #555555;
    --slate: #2f3e46;
    --rust: #6b1a12;
    --amber: #e08a2a;
    --gold: #f6c24a;
    --sand: #c9a273;
    --sand-light: #e6c9a0;
    --fb: #3b5998;
    --tw: #2aa3ef;
    --yt: #e52d27;
  }
  * { box-sizing: border-box; margin: 0; padding: 0; }
  html, body { width: 1200px; height: 1200px; overflow: hidden; }
  body {
    background: var(--stage);
    font-family: "Source Sans 3", sans-serif;
    position: relative;
  }
  .card {
    position: absolute;
    top: 198px;
    width: 571px;
    height: 804px;
    overflow: hidden;
    background: var(--white);
    box-shadow: 4px 4px 10px rgba(0,0,0,.35);
  }
  .card--front { left: 21px; }
  .card--back { left: 609px; }
  .abs { position: absolute; }

  /* Front */
  .photo-treatment {
    left: 0; top: 0; width: 571px; height: 340px;
    background: linear-gradient(135deg, #8a6a4c 0%, var(--sand) 45%, var(--sand-light) 100%);
  }
  .photo-people {
    left: 0; top: 300px; width: 571px; height: 504px;
    background: linear-gradient(160deg, #e9c9a0 0%, #c4956a 40%, #5a4a40 75%, #2a2420 100%);
  }
  .wash {
    left: 0; top: 300px; width: 571px; height: 504px;
    background: linear-gradient(90deg, rgba(248,248,248,.96) 0%, rgba(248,248,248,.85) 45%, rgba(248,248,248,0) 70%);
  }
  .wave { left: 0; top: 0; }
  .brand {
    left: 350px; top: 40px; width: 190px;
    display: flex; flex-direction: column; align-items: center; gap: 8px;
    color: var(--white); text-align: center;
  }
  .brand__dot { width: 34px; height: 34px; border-radius: 50%; border: 3px solid var(--white); }
  .brand__name { font-weight: 700; font-size: 25px; line-height: 24px; }
  .title {
    left: 198px; top: 162px; font-weight: 300; font-size: 37px; color: var(--white);
  }
  .section-head {
    display: flex; align-items: center; gap: 14px;
    font-weight: 700; font-size: 19px; color: var(--ink); letter-spacing: .3px;
  }
  .section-head__mark {
    width: 22px; height: 22px; border-radius: 50%;
    background: linear-gradient(135deg, var(--gold), var(--amber));
    margin-left: 20px;
  }
  .copy { font-size: 16.5px; line-height: 20.8px; color: var(--ink); width: 250px; }
  .copy--light { color: var(--white); }
  .quote-bar {
    left: 0; top: 676px; width: 571px; height: 92px;
    background: rgba(245,245,245,.9);
  }
  .quote-bar__icon { left: 34px; top: 22px; }
  .quote-bar__lead { left: 96px; top: 20px; font-size: 19px; color: var(--ink); }
  .quote-bar__lead b { font-weight: 700; }
  .quote-bar__number { left: 96px; top: 40px; font-size: 37px; font-weight: 700; color: var(--ink); }

  /* Back */
  .more { left: 0; top: 168px; width: 571px; text-align: center; font-size: 38px; color: var(--grey-text); }
  .hours { left: 66px; top: 466px; font-size: 16.5px; line-height: 20.8px; color: var(--ink); }
  .hours td { padding-right: 14px; }
  .address { left: 66px; top: 578px; font-size: 18.5px; line-height: 23px; color: var(--ink); }
  .social { left: 401px; top: 575px; display: flex; gap: 2px; }
  .social span { width: 42px; height: 42px; border-radius: 50%; border: 2px solid var(--white); }
  .contact { left: 255px; top: 690px; color: var(--white); font-size: 19px; }
  .contact li { list-style: none; display: flex; align-items: center; gap: 10px; height: 30px; }
</style>
</head>
<body>

<section class="card card--front">
  <div class="abs photo-people" role="img" aria-label="Photo of a smiling young couple relaxing outdoors at sunset"></div>
  <div class="abs wash"></div>
  <div class="abs photo-treatment" role="img" aria-label="Photo of acupuncture needles being placed on a client's shoulder"></div>

  <svg class="abs wave" width="571" height="804" viewBox="0 0 571 804">
    <defs>
      <linearGradient id="front-band" x1="0" x2="1">
        <stop offset="0" stop-color="var(--rust)"/>
        <stop offset=".6" stop-color="#8a2a14"/>
        <stop offset=".85" stop-color="var(--amber)"/>
        <stop offset="1" stop-color="var(--gold)"/>
      </linearGradient>
    </defs>
    <path d="M0 258 C140 236 280 250 380 288 C460 318 530 318 571 300 L571 350 C500 346 440 330 380 306 C260 262 120 262 0 300 Z" fill="url(#front-band)"/>
    <path d="M0 264 C140 244 280 262 370 296 C440 322 510 318 571 286 L571 292 C520 326 450 330 370 302 C260 264 130 262 0 302 Z" fill="var(--white)"/>
    <path d="M0 300 C120 262 260 262 380 306 C440 330 500 346 571 350 L571 360 L0 360 Z" fill="#f8f8f8"/>
  </svg>

  <div class="abs brand">
    <span class="brand__dot"></span>
    <span class="brand__name">Thornbury<br>Accupuncture</span>
  </div>
  <h1 class="abs title">Additional Title Here</h1>

  <h2 class="abs section-head" style="left:0;top:312px"><span class="section-head__mark"></span>ABOUT US</h2>
  <p class="abs copy" style="left:48px;top:350px">Lorem ipsum dolor sit amet, consectetur adipiscing elit. Sed tempus orci turpis, sit amet ultricies tellus aliquet in. Nullam at suscipit nisl, vel interdum est. Vestibulum et placerat ipsum, vitae.</p>

  <h2 class="abs section-head" style="left:0;top:526px"><span class="section-head__mark"></span>OUR MISSION</h2>
  <p class="abs copy copy--light" style="left:48px;top:568px">Lorem ipsum dolor sit amet, consectetur adipiscing elit. Sed tempus orci turpis, sit amet ultricies tellus aliquet in.</p>

  <div class="abs quote-bar">
    <svg class="abs quote-bar__icon" width="52" height="50" viewBox="0 0 52 50">
      <path d="M8 4 C4 8 4 16 12 26 C20 36 30 42 36 40 L42 36 L34 26 L28 30 C24 28 18 22 16 16 L20 10 L12 2 Z" fill="var(--ink)"/>
      <path d="M2 44 l4 -4 l3 4 l3 -4 l3 4 l3 -4 l3 4" fill="none" stroke="var(--ink)" stroke-width="1.5"/>
    </svg>
    <p class="abs quote-bar__lead"><b>FREE QUOTE</b> CALL OR TEXT</p>
    <p class="abs quote-bar__number">888-888-8888</p>
  </div>
</section>

<section class="card card--back">
  <h2 class="abs more">More Content Here</h2>

  <h3 class="abs section-head" style="left:20px;top:428px"><span class="section-head__mark"></span>HOURS</h3>
  <table class="abs hours">
    <tr><td>Monday to Friday</td><td>9:00 AM – 7:00 PM</td></tr>
    <tr><td>Saturday</td><td>9:00 AM – 3:00 PM</td></tr>
  </table>

  <h3 class="abs section-head" style="left:20px;top:540px"><span class="section-head__mark"></span>LOCATION</h3>
  <p class="abs address">Unit, Street, City<br>State, Zip Code</p>

  <h3 class="abs section-head" style="left:335px;top:540px"><span class="section-head__mark"></span>FIND US ON</h3>
  <div class="abs social">
    <span style="background:var(--fb)"></span>
    <span style="background:var(--tw)"></span>
    <span style="background:var(--yt)"></span>
  </div>

  <svg class="abs wave" width="571" height="804" viewBox="0 0 571 804">
    <defs>
      <linearGradient id="back-band" x1="0" x2="1">
        <stop offset="0" stop-color="var(--amber)"/>
        <stop offset=".55" stop-color="var(--gold)"/>
        <stop offset=".8" stop-color="#f3d98a"/>
        <stop offset="1" stop-color="var(--amber)"/>
      </linearGradient>
    </defs>
    <path d="M325 644 C420 630 510 640 571 660 L571 688 C500 660 420 648 325 644 Z" fill="url(#back-band)"/>
    <path d="M0 714 C110 714 200 690 280 666 C380 640 490 650 571 688 L571 804 L0 804 Z" fill="var(--slate)"/>
  </svg>

  <ul class="abs contact">
    <li>
      <svg width="20" height="20" viewBox="0 0 20 20"><path d="M4 2 C2 4 2 8 6 13 C10 18 15 19 17 17 L18 15 L14 11 L12 13 C10 12 8 10 7 8 L9 6 L5 2 Z" fill="none" stroke="var(--white)" stroke-width="1.4"/></svg>
      888-888-8888
    </li>
    <li>
      <svg width="20" height="20" viewBox="0 0 20 20"><rect x="1.5" y="4" width="17" height="12" fill="none" stroke="var(--white)" stroke-width="1.4"/><path d="M1.5 4 L10 11 L18.5 4" fill="none" stroke="var(--white)" stroke-width="1.4"/></svg>
      name@email.com
    </li>
    <li>
      <svg width="20" height="20" viewBox="0 0 20 20"><path d="M2 10 L10 2 L18 10 M4.5 8 V18 H8 V12 H12 V18 H15.5 V8" fill="none" stroke="var(--white)" stroke-width="1.4"/></svg>
      domain.com
    </li>
  </ul>
</section>

</body>
</html>
```